Fight Deflation with Seasonal General Merchandise - Tall Pine Traders & Advisors, Inc.

We are looking to create a Business to Business Advertising Concept that will appear in various trade publications within the US Supermarket Industry. The final concept will be adapted to be used in print, digital and direct mail mediums. For purposes of your submissions, please design as if it is for a 8.5" x 11" (vertical) print ad.

Using the creative elements and images attached for direction and inspiration, please submit your best concepts. The high resolution images shown have already been purchased from a stock photo house with the rights to use them for this campaign. While we like these images as well as the headlines provided, feel free to add your own suggestions or creativity if you wish.

Primarily, however, we'd like you to take the existing headlines and images and build off of them, incorporating solid use of font/text treatment and improving upon overall layout of the ad so that the end result is professional and engaging to the audience.

A note about the concept: Tall Pine Traders supplies US Grocery Store Chains with Seasonal General Merchandise. Currently and for the foreseeable future, grocers are battling the effects of deflationary pricing on key commodities such as Eggs/Dairy; Meat; Produce, etc... The result of this is that grocery prices are significantly lower than last year. While this is good for the consumers, it is not ideal for the retailers as they are making fewer sales and profits while selling the same or more product. The products Tall Pine Trader's sells to these grocers can help the retailer offset these lower prices by adding "incremental" sales and profits to the retailer. Our products range from items like Christmas decor and gift wrap, to outdoor items like patio furniture and grills. We are focusing on the Christmas theme because the ads will drop starting late November.

Target Market(s)

Senior Buyers and Top Executives at US Based Grocery Store Chains.

Industry/Entity Type

Business

Requirements
Must have
• See Project Description
• Open to all colors and fonts.
Nice to have
• See Project Description
Should not have
• See Project Description

```html
<!DOCTYPE html>
<html lang="en">
<head>
<meta charset="utf-8">
<title>Tall Pine Traders – Seasonal General Merchandise Ad</title>
<link rel="stylesheet" href="https://fonts.googleapis.com/css2?family=Oswald:wght@700&family=Hind:wght@400;600;700&display=swap">
<style>
  :root {
    --page-bg: #e9e9e9;
    --blue-deep: #0b86d3;
    --blue-light: #2fb3f0;
    --red-bright: #e3171c;
    --red-deep: #b0080c;
    --band-gray: #4a4a4c;
    --band-white: #ffffff;
    --text-light: #ffffff;
  }
  * { margin: 0; padding: 0; box-sizing: border-box; }
  html, body { width: 1000px; height: 1200px; overflow: hidden; }
  body {
    background: var(--page-bg);
    font-family: "Hind", Arial, sans-serif;
    color: var(--text-light);
    position: relative;
  }
  .ad {
    position: absolute;
    left: 60px; top: 30px;
    width: 880px; height: 1140px;
    overflow: hidden;
  }
  .ad-shapes { position: absolute; inset: 0; }
  .headline {
    position: absolute;
    left: 57px; top: 50px;
    font-family: "Oswald", "Arial Narrow", sans-serif;
    font-weight: 700;
    font-size: 46px;
    letter-spacing: 0.2px;
    line-height: 1;
    white-space: nowrap;
  }
  .subhead {
    position: absolute;
    left: 57px; top: 126px;
    width: 370px;
    font-size: 25px;
    font-weight: 600;
    line-height: 30px;
  }
  .brand {
    position: absolute;
    left: 474px; top: 872px;
    display: flex; align-items: center; gap: 12px;
  }
  .brand-mark {
    width: 60px; height: 62px;
    background: var(--text-light);
    flex: none;
  }
  .brand-name {
    font-size: 28px;
    font-weight: 700;
    line-height: 1;
    white-space: nowrap;
  }
  .showroom {
    position: absolute;
    left: 66px; top: 928px;
    font-size: 21px;
    line-height: 28px;
    font-weight: 400;
  }
  .phone-icon {
    position: absolute;
    left: 697px; top: 972px;
    width: 50px; height: 50px;
  }
  .phone-number {
    position: absolute;
    left: 612px; top: 1036px;
    width: 224px;
    text-align: center;
    font-size: 30px;
    font-weight: 700;
    letter-spacing: 0.5px;
    white-space: nowrap;
  }
  .contact {
    position: absolute;
    left: 66px; top: 1088px;
    font-size: 18px;
    display: flex; gap: 20px; align-items: center;
    white-space: nowrap;
  }
  .contact strong { font-weight: 700; }
  .contact .email { display: flex; align-items: center; gap: 6px; }
</style>
</head>
<body>
  <div class="ad">
    <svg class="ad-shapes" viewBox="0 0 880 1140" width="880" height="1140">
      <defs>
        <linearGradient id="blueFill" x1="0" y1="0" x2="0" y2="1">
          <stop offset="0" stop-color="var(--blue-deep)"/>
          <stop offset="1" stop-color="var(--blue-light)"/>
        </linearGradient>
        <linearGradient id="redFill" x1="0" y1="0" x2="1" y2="1">
          <stop offset="0" stop-color="var(--red-bright)"/>
          <stop offset="1" stop-color="var(--red-deep)"/>
        </linearGradient>
        <linearGradient id="photoFill" x1="0.2" y1="0" x2="0.4" y2="1">
          <stop offset="0" stop-color="#d8d3c8"/>
          <stop offset="0.3" stop-color="#ece8df"/>
          <stop offset="0.5" stop-color="#f5f2ec"/>
          <stop offset="0.68" stop-color="#cbb894"/>
          <stop offset="0.85" stop-color="#a08a62"/>
          <stop offset="1" stop-color="#6f5f44"/>
        </linearGradient>
      </defs>

      <rect class="photo-area" x="0" y="140" width="880" height="720" fill="url(#photoFill)"
            role="img" aria-label="Photo: white eggs in a clear amber egg carton, one wearing a small Santa hat, with white snowflake decorations behind"/>

      <!-- top wave bands -->
      <path class="band-red" fill="url(#redFill)" d="M0,0 H880 V205 C600,225 300,395 0,322 Z"/>
      <path class="band-gray" fill="var(--band-gray)" d="M0,0 H880 V190 C600,210 300,375 0,295 Z"/>
      <path class="band-white" fill="var(--band-white)" d="M0,0 H880 V178 C600,198 300,360 0,276 Z"/>
      <path class="header-blue" fill="url(#blueFill)" d="M0,0 H880 V160 C600,180 300,340 0,250 Z"/>

      <!-- bottom wave bands -->
      <path class="band-blue" fill="var(--blue-deep)" d="M0,800 C300,830 600,710 880,700 V1140 H0 Z"/>
      <path class="band-gray" fill="var(--band-gray)" d="M0,822 C300,852 600,732 880,722 V1140 H0 Z"/>
      <path class="band-white" fill="var(--band-white)" d="M0,836 C300,866 600,746 880,736 V1140 H0 Z"/>
      <path class="footer-red" fill="url(#redFill)" d="M0,872 C300,895 600,800 880,790 V1140 H0 Z"/>
    </svg>

    <h1 class="headline">SCRAMBLING TO DEAL WITH DEFLATION?</h1>
    <p class="subhead">Hatch Eggstraordinary Profits with Seasonal General Merchandise!</p>

    <div class="brand">
      <span class="brand-mark"></span>
      <span class="brand-name">Tall Pine Traders<br>and Advisors, Inc.</span>
    </div>

    <p class="showroom">
      Visit our exciting Fall/Winter<br>
      2017 Showroom representing<br>
      over 4,000 items from 350 factories<br>
      Scheduling appointments now for<br>
      January - March, 2017
    </p>

    <svg class="phone-icon" viewBox="0 0 48 48" aria-hidden="true">
      <circle cx="24" cy="24" r="21" fill="none" stroke="var(--text-light)" stroke-width="3"/>
      <path fill="var(--text-light)" d="M17.5 13.5c1-.6 2.2-.3 2.8.7l2 3.4c.5.9.3 2-.5 2.6l-1.5 1.1c.9 2.3 2.6 4.2 4.8 5.4l1.2-1.4c.7-.8 1.8-.9 2.6-.4l3.3 2.2c1 .6 1.2 1.9.6 2.8l-1 1.5c-.9 1.3-2.5 1.9-4 1.5-6.4-1.8-11.2-7-12.6-13.5-.3-1.5.3-3 1.6-3.9z"/>
    </svg>
    <p class="phone-number">555-014-2870</p>

    <p class="contact">
      <span><strong>Contact Dana Whitfield,</strong></span>
      <span>VP Business Development at</span>
      <span class="email">
        <svg width="14" height="10" viewBox="0 0 14 10" aria-hidden="true"><rect x="0.7" y="0.7" width="12.6" height="8.6" fill="none" stroke="#fff" stroke-width="1.2"/><path d="M0.7 0.7 7 5.5 13.3 0.7" fill="none" stroke="#fff" stroke-width="1.2"/></svg>
        dwhitfield@tallpinetraders.com
      </span>
    </p>
  </div>
</body>
</html>
```